Executive Business Card for Healthcare Company [Need Today]

I need a business card design for a healthcare company. The only branding the company has thus far is a logo. The cards will be utilized by company executives. The design I envision will be vibrant and appealing but with a corporate feel. They shouldn't be too casual or playful. I would like to complete this project TODAY if possible.

Target Market(s)

Healthcare vendors, other executives in healthcare and pharmaceuticals

Industry/Entity Type

Pharmaceutical

Contact Information for Business Card

See attachment

Font styles to use
Serif
Sans Serif

Colors

Designer to choose colors to be used in the design.

```html
<!DOCTYPE html>
<html lang="en">
<head>
<meta charset="utf-8">
<title>Corvane Therapeutics — Business Card</title>
<link rel="stylesheet" href="https://fonts.googleapis.com/css2?family=Questrial&display=swap">
<style>
  :root {
    --backdrop: #1d1d1f;
    --teal: #38bfc7;
    --teal-text: #2fb6c2;
    --green: #5cc08f;
    --grey: #5f6163;
    --paper: #ffffff;
    --ring-light: rgba(255,255,255,0.2);
    --ring-faint: #eef6f3;
    --rule: #3cbfc9;
  }
  * { box-sizing: border-box; margin: 0; padding: 0; }
  html, body {
    width: 1189px; height: 1200px; overflow: hidden;
    background: var(--backdrop);
    font-family: "Questrial", "Century Gothic", sans-serif;
  }
  .card {
    position: absolute; left: 164px;
    width: 860px; height: 490px;
    overflow: hidden;
  }
  .card--front { top: 70px; background: var(--teal); }
  .card--back { top: 630px; background: var(--paper); }

  .deco-ring {
    position: absolute; border-radius: 50%;
  }
  .card--front .deco-ring {
    left: -146px; top: -1px; width: 474px; height: 474px;
    border: 12px solid var(--ring-light);
  }
  .card--back .deco-ring {
    left: -8px; top: -30px; width: 376px; height: 376px;
    border: 10px solid var(--ring-faint);
  }

  .brand {
    position: absolute; display: flex; align-items: center;
  }
  .brand__mark {
    width: 114px; height: 114px; border-radius: 50%;
    border: 4px solid currentColor; flex: none;
  }
  .brand__divider {
    width: 2px; height: 56px; margin: 0 12px 0 14px; flex: none;
  }
  .brand__name {
    font-size: 40px; line-height: 1.05; letter-spacing: 0.5px;
  }
  .card--front .brand { left: 248px; top: 188px; color: #fff; }
  .card--front .brand__divider { background: rgba(255,255,255,0.85); }
  .card--front .brand__name { color: #fff; }

  .card--back .brand { left: 441px; top: 54px; }
  .card--back .brand__mark { color: var(--green); }
  .card--back .brand__divider { background: #b9bcbd; }
  .card--back .brand__name { color: var(--teal-text); font-size: 36px; }

  .tab-dot {
    position: absolute; left: -24px; top: 61px;
    width: 48px; height: 48px; border-radius: 50%;
    background: var(--teal);
  }
  .person { position: absolute; left: 46px; top: 60px; }
  .person__name { color: var(--teal-text); font-size: 27px; line-height: 1.1; }
  .person__title { color: var(--grey); font-size: 20.5px; line-height: 1.1; }

  .rule {
    position: absolute; left: 46px; top: 351px;
    width: 757px; height: 1px; background: var(--rule);
  }
  .contacts {
    position: absolute; left: 46px; top: 367px;
    list-style: none; color: var(--grey); font-size: 21px;
  }
  .contacts li { display: flex; align-items: center; height: 27px; }
  .contacts svg { width: 22px; height: 22px; margin-right: 8px; flex: none; }
  .company {
    position: absolute; left: 572px; top: 367px;
    font-style: normal; color: var(--grey); font-size: 21px; line-height: 27px;
  }
  .company__name { color: var(--teal-text); }
</style>
</head>
<body>
  <section class="card card--front" aria-label="Card front">
    <div class="deco-ring"></div>
    <div class="brand">
      <span class="brand__mark"></span>
      <span class="brand__divider"></span>
      <span class="brand__name">corvane therapeutics</span>
    </div>
  </section>

  <section class="card card--back" aria-label="Card back">
    <div class="deco-ring"></div>
    <span class="tab-dot"></span>
    <div class="person">
      <p class="person__name">Martin Hale</p>
      <p class="person__title">Senior Director of Marketing</p>
    </div>
    <div class="brand">
      <span class="brand__mark"></span>
      <span class="brand__divider"></span>
      <span class="brand__name">corvane therapeutics</span>
    </div>
    <div class="rule"></div>
    <ul class="contacts">
      <li>
        <svg viewBox="0 0 22 22" aria-hidden="true"><circle cx="11" cy="11" r="10" fill="none" stroke="#5cc08f" stroke-width="1.6"/><rect x="7.5" y="5" width="7" height="12" rx="1.2" fill="none" stroke="#5cc08f" stroke-width="1.5"/><line x1="10" y1="15" x2="12" y2="15" stroke="#5cc08f" stroke-width="1.2"/></svg>
        555-210-4837
      </li>
      <li>
        <svg viewBox="0 0 22 22" aria-hidden="true"><circle cx="11" cy="11" r="10" fill="#5cc08f"/><path d="M5.5 10c0-2 2.5-3 5.5-3s5.5 1 5.5 3l-2 .6-.6-1.6h-5.8l-.6 1.6z M7.5 11h7l1 4h-9z" fill="#fff"/></svg>
        555-210-6652
      </li>
      <li>
        <svg viewBox="0 0 22 22" aria-hidden="true"><circle cx="11" cy="11" r="10" fill="#5cc08f"/><rect x="5.5" y="7" width="11" height="8" fill="#fff"/><path d="M5.5 7l5.5 4.5L16.5 7M5.5 15l4-4M16.5 15l-4-4" fill="none" stroke="#5cc08f" stroke-width="1"/></svg>
        mhale@corvanerx.com
      </li>
    </ul>
    <address class="company">
      <span class="company__name">Corvane Therapeutics, LLC</span><br>
      118 N Linden Avenue<br>
      Milford, OH 45150
    </address>
  </section>
</body>
</html>
```